Additional Benefits of Working for VELMAR

Please prepare an infographic on the additional benefits besides salary of working at VELMAR as detailed in the attached word document. Also attached is our logo in eps and our company design "Grounds". We are a Not For Profit company that finds jobs for unemployed people of government benefit payments

Target Market(s)

Attracting people to work for VELMAR. Making VELMAR an employer of choice.

Font styles to use
Sans Serif

Colors

Designer to choose colors to be used in the design.

Requirements
Must have
• be on 1 page
• have our logo
Nice to have
• Our Grounds design worked into it.
• Happy engaged employees
• Community engagement - we are a not for profit organisation
Should not have
• Discrimination, swearing,

```html
<!DOCTYPE html>
<html lang="en">
<head>
<meta charset="utf-8">
<title>The Benefits of Working with Us – VELMAR</title>
<link href="https://fonts.googleapis.com/css2?family=Poppins:wght@500;600&family=Roboto:wght@400;500&display=swap" rel="stylesheet">
<style>
:root{
  --green-dark:#0f7a5c;
  --green:#1a9474;
  --green-light:#5fb89a;
  --gold:#c98a2e;
  --gold-light:#e9c285;
  --gold-deep:#b97a22;
  --ink:#111;
  --frame:#555;
  --white:#fff;
}
*{margin:0;padding:0;box-sizing:border-box}
html,body{width:1200px;height:990px;overflow:hidden;background:var(--white)}
.sheet{
  position:absolute;left:252px;top:11px;width:633px;height:880px;
  border:1px solid var(--frame);background:var(--white);
  transform:scale(1.1);transform-origin:0 0;
  font-family:"Roboto",Arial,sans-serif;color:var(--ink);
}
.title-band{
  position:absolute;left:46px;top:24px;width:576px;height:68px;border-radius:24px;
  background:linear-gradient(170deg,var(--green-light) 0%,var(--green) 45%,var(--green-dark) 100%);
  color:var(--white);font-family:"Poppins",Arial,sans-serif;font-weight:500;
  font-size:34px;line-height:68px;padding-left:14px;letter-spacing:.3px;white-space:nowrap;
}
.ribbon{
  position:absolute;height:32px;
  background:linear-gradient(180deg,var(--gold-light) 0%,var(--gold) 55%,var(--gold-deep) 100%);
  clip-path:polygon(0 0,100% 0,calc(100% - 14px) 100%,0 100%);
}
.ribbon.right{border-radius:16px 0 0 16px;clip-path:polygon(0 0,100% 0,calc(100% - 14px) 100%,0 100%)}
.heading{
  position:absolute;font-family:"Poppins",Arial,sans-serif;font-weight:600;font-size:19px;
  line-height:25px;white-space:nowrap;color:var(--gold);letter-spacing:.3px;
}
.heading .on-ribbon{color:var(--white)}
.badge{
  position:absolute;width:64px;height:64px;border-radius:50%;
  background:var(--white);border:3px solid var(--green);
  display:flex;align-items:center;justify-content:center;
}
.badge svg{width:40px;height:40px;fill:none;stroke:var(--green-dark);stroke-width:2.2;stroke-linecap:round;stroke-linejoin:round}
.points{position:absolute;list-style:none;font-size:8.6px;line-height:11.4px}
.points li{margin-bottom:4px}
.points li::before{content:"• "}
.points.large{font-size:10.2px;line-height:14px}
.points.large li{margin-bottom:6px}
</style>
</head>
<body>
<main class="sheet">
  <h1 class="title-band">The Benefits of Working with Us</h1>

  <!-- Life Balance -->
  <div class="ribbon" style="left:0;top:123px;width:257px"></div>
  <div class="badge" style="left:15px;top:105px">
    <svg viewBox="0 0 40 40"><line x1="20" y1="6" x2="20" y2="33"/><line x1="8" y1="12" x2="32" y2="12"/><path d="M8 12 L3 22 H13 Z"/><path d="M32 12 L27 22 H37 Z"/><line x1="13" y1="34" x2="27" y2="34"/><circle cx="20" cy="6" r="2"/></svg>
  </div>
  <h2 class="heading" style="left:90px;top:127px"><span class="on-ribbon">Life Balance</span></h2>
  <ul class="points" style="left:60px;top:178px;width:200px">
    <li>VELMAR Day Leave. An extra day of at Christmas</li>
    <li>BIRTHDAY Leave. A paid day off on your birthday</li>
    <li>A day off every month as Time In Lieu</li>
    <li>4 weeks Annual Leave</li>
    <li>Genereous Personal Leave</li>
    <li>Support for parental leave for the birth or adoption of a child</li>
    <li>Flexible work arrangements</li>
  </ul>

  <!-- Wellbeing -->
  <div class="ribbon" style="left:0;top:338px;width:252px"></div>
  <div class="badge" style="left:15px;top:320px">
    <svg viewBox="0 0 40 40"><path d="M20 34 C8 25 3 19 3 12 C3 7 7 4 11.5 4 C15 4 18 6 20 9 C22 6 25 4 28.5 4 C33 4 37 7 37 12 C37 19 32 25 20 34 Z"/><path d="M20 29 C11 22 8 18 8 13 C8 10 10 8.5 12.5 8.5"/></svg>
  </div>
  <h2 class="heading" style="left:94px;top:342px"><span class="on-ribbon">Wellbeing</span></h2>
  <ul class="points" style="left:60px;top:387px;width:190px">
    <li>Up to $450 per year to spend on Wellbeing services such as gym or yoga memberships</li>
    <li>Free counselling services 24x7 via our Employee Assistance Program</li>
    <li>Discount private health insurance</li>
    <li>WHS policies which suppor a safe, inclusive work place</li>
  </ul>

  <!-- Career Growth -->
  <div class="ribbon" style="left:0;top:518px;width:255px"></div>
  <div class="badge" style="left:15px;top:500px">
    <svg viewBox="0 0 40 40"><path d="M4 4 V36 H36"/><line x1="10" y1="34" x2="10" y2="24"/><line x1="15" y1="34" x2="15" y2="20"/><line x1="20" y1="34" x2="20" y2="22"/><line x1="25" y1="34" x2="25" y2="16"/><line x1="30" y1="34" x2="30" y2="12"/><path d="M8 22 L17 13 L22 17 L33 6"/><path d="M27 6 H33 V12"/></svg>
  </div>
  <h2 class="heading" style="left:84px;top:522px"><span class="on-ribbon">Career Growth</span><br>&amp;Professional<br>Development</h2>
  <ul class="points" style="left:60px;top:606px;width:190px">
    <li>Ongoing internal training and development opportunities</li>
    <li>External srudy support § study leave</li>
    <li>Access to the tools and technology to do your job well</li>
    <li>Career advancement opportunities</li>
    <li>Internal job vacancy listing</li>
  </ul>

  <!-- Remuneration -->
  <div class="ribbon" style="left:0;top:717px;width:255px"></div>
  <div class="badge" style="left:15px;top:699px">
    <svg viewBox="0 0 40 40"><rect x="6" y="5" width="28" height="30" rx="2"/><line x1="6" y1="11" x2="34" y2="11"/><path d="M34 18 H25 V27 H34"/><circle cx="29" cy="22.5" r="1.3"/></svg>
  </div>
  <h2 class="heading" style="left:84px;top:721px"><span class="on-ribbon">Remuneration</span><br>&amp; Salary Packaging</h2>
  <ul class="points" style="left:60px;top:782px;width:195px">
    <li>Competetive salary</li>
    <li>Ability to salary package up to $15,900 and reduce your tax. Package rent, home loans, child care and much more</li>
    <li>Salary package up to $2,650 on meal entertainment and holiday accommodation</li>
  </ul>

  <!-- Diversity & Inclusion -->
  <div class="ribbon right" style="left:312px;top:181px;width:256px"></div>
  <div class="badge" style="left:326px;top:163px">
    <svg viewBox="0 0 40 40"><circle cx="20" cy="11" r="6"/><path d="M6 36 C6 26 12 21 20 21 C28 21 34 26 34 36 Z"/><path d="M14 24 L20 31 L26 24"/></svg>
  </div>
  <h2 class="heading" style="left:400px;top:185px"><span class="on-ribbon">Diversity &amp;</span><br>Inclusion</h2>
  <ul class="points" style="left:372px;top:248px;width:185px">
    <li>An inclusive and diverse culture where different backgounds, experiences and perspectives are valued</li>
    <li>Gender diversity. Over 50% of our workforce and our leaders are female</li>
  </ul>

  <!-- Benefits -->
  <div class="ribbon right" style="left:307px;top:330px;width:256px"></div>
  <div class="badge" style="left:321px;top:313px">
    <svg viewBox="0 0 40 40"><path d="M3 6 H9 L13 26 H32 L35 12 H10"/><line x1="12" y1="19" x2="34" y2="19"/><line x1="18" y1="12" x2="19" y2="26"/><line x1="26" y1="12" x2="25" y2="26"/><circle cx="15" cy="32" r="2.2"/><circle cx="29" cy="32" r="2.2"/></svg>
  </div>
  <h2 class="heading" style="left:395px;top:334px"><span class="on-ribbon">Benefits</span></h2>
  <ul class="points" style="left:367px;top:378px;width:190px">
    <li>Discounted vouchers for Harvest Foods, Dailyway, TechBarn, Reelhouse, Cellar Lane, ValueCo, Outfitters Co and many others via Paywise e-wallet</li>
    <li>A range of other employee discounts are also available, including access to discounted bankin and finance, vehicle purchasing, leasing and hotel accomodation</li>
  </ul>

  <!-- Recognition -->
  <div class="ribbon right" style="left:312px;top:497px;width:256px"></div>
  <div class="badge" style="left:323px;top:481px">
    <svg viewBox="0 0 40 40"><path d="M12 4 H28 V14 L20 19 L12 14 Z"/><line x1="17" y1="4" x2="17" y2="16"/><line x1="23" y1="4" x2="23" y2="16"/><circle cx="20" cy="27" r="9"/><path d="M20 21.5 L21.7 25 L25.5 25.4 L22.6 27.9 L23.5 31.6 L20 29.7 L16.5 31.6 L17.4 27.9 L14.5 25.4 L18.3 25 Z"/></svg>
  </div>
  <h2 class="heading" style="left:400px;top:501px"><span class="on-ribbon">Recognition</span></h2>
  <ul class="points large" style="left:372px;top:539px;width:200px">
    <li>We celebrate our people forreaching service milestones</li>
    <li>Team &amp; individual recognition for high performance</li>
  </ul>

  <!-- Community -->
  <div class="ribbon right" style="left:312px;top:623px;width:256px"></div>
  <div class="badge" style="left:323px;top:607px">
    <svg viewBox="0 0 40 40"><circle cx="20" cy="20" r="15"/><ellipse cx="20" cy="20" rx="7" ry="15"/><line x1="20" y1="5" x2="20" y2="35"/><line x1="5" y1="20" x2="35" y2="20"/><path d="M7.5 12 H32.5 M7.5 28 H32.5"/></svg>
  </div>
  <h2 class="heading" style="left:400px;top:627px"><span class="on-ribbon">Contributing to</span><br>Community</h2>
  <ul class="points" style="left:372px;top:692px;width:190px">
    <li>Team involvement in local charity and community events</li>
    <li>Participation in VELMAR's 1000 Jobs in 100 days</li>
    <li>Strong relationships and connection with Indigenous Communities in support of Indigenous Emplyment</li>
  </ul>
</main>
</body>
</html>
```